New Zealand Marlborough Sauvignon Blanc wine packaging design

We need packaging design for our new wine brand, Dunmore Vale. The wine is a New Zealand Marlborough Sauvignon Blanc. We would like the packaging will portray elegance and style with an understated label. We are looking for a label that portrays the elegance of the French Riviera. The label should be round or pill shaped.
Updates

Industry/Entity Type

Wine

Font styles to use
Serif
Sans Serif

Requirements
Must have
• The words in order of importance: Dunmore Vale, Sauvignon Blanc, Marlborough, New Zealand. It should be fit to the bottle posted in the links
Nice to have
• a pill shape or circular shape
Should not have
• Illustrations of wine bottles, wine glasses, or grapes

```html
<!DOCTYPE html>
<html lang="en">
<head>
<meta charset="utf-8">
<title>Dunmore Vale – Marlborough Sauvignon Blanc Label</title>
<link rel="stylesheet" href="https://fonts.googleapis.com/css2?family=Cinzel:wght@700&family=Cinzel+Decorative:wght@700&display=swap">
<style>
  :root {
    --gold: #a8843f;
    --ink: #131b1d;
    --paper: #ffffff;
    --backdrop: #ffffff;
    --rule-tone: #7d8284;
  }
  html, body {
    margin: 0;
    padding: 0;
    width: 1200px;
    height: 1056px;
    overflow: hidden;
    background: var(--backdrop);
  }
  .canvas {
    position: relative;
    width: 1200px;
    height: 1056px;
  }
  .wine-label {
    position: absolute;
    left: 246px;
    top: 72px;
    width: 707px;
    height: 911px;
  }
  .brand-name {
    font-family: "Cinzel", "Times New Roman", serif;
    font-weight: 700;
    fill: var(--gold);
  }
  .varietal-line {
    font-family: "Cinzel Decorative", "Times New Roman", serif;
    font-weight: 700;
    fill: var(--paper);
    letter-spacing: 7px;
  }
  .vintage {
    font-family: "Cinzel", "Times New Roman", serif;
    font-weight: 700;
    fill: var(--gold);
    letter-spacing: 6px;
  }
  .cuvee-note {
    font-family: "Cinzel", "Times New Roman", serif;
    font-weight: 700;
    fill: var(--gold);
    letter-spacing: 5px;
  }
</style>
</head>
<body>
<main class="canvas">
  <svg class="wine-label" viewBox="0 0 1140 1470" xmlns="http://www.w3.org/2000/svg">
    <defs>
      <path id="brand-arc" d="M 150 1000 L 150 640 C 150 340 340 168 570 168 C 800 168 990 340 990 640 L 990 1000"/>
      <linearGradient id="rule-tone-left" x1="0" y1="0" x2="1" y2="0">
        <stop offset="0" stop-color="var(--paper)"/>
        <stop offset="1" stop-color="var(--rule-tone)"/>
      </linearGradient>
      <linearGradient id="rule-tone-right" x1="1" y1="0" x2="0" y2="0">
        <stop offset="0" stop-color="var(--paper)"/>
        <stop offset="1" stop-color="var(--rule-tone)"/>
      </linearGradient>
    </defs>

    <path class="label-body" d="M 10 1060 L 10 640 C 10 250 250 10 570 10 C 890 10 1130 250 1130 640 L 1130 1060 Z"
          fill="var(--paper)" stroke="var(--ink)" stroke-width="12"/>

    <path class="arch-frame" d="M 185 1045 L 185 560 C 185 330 360 182 570 182 C 780 182 955 330 955 560 L 955 1045"
          fill="none" stroke="var(--ink)" stroke-width="12"/>
    <path class="arch-frame-inner" d="M 212 1045 L 212 575 C 212 360 375 212 570 212 C 765 212 928 360 928 575 L 928 1045"
          fill="none" stroke="var(--ink)" stroke-width="4"/>

    <path class="coastal-scene" role="img" aria-label="Engraved view of a hillside village above a Riviera bay in gold"
          d="M 224 1045 L 224 580 C 224 370 380 224 570 224 C 760 224 916 370 916 580 L 916 1045 Z"
          fill="var(--gold)" opacity="0.85"/>

    <path class="rule-ornament rule-ornament-left" role="img" aria-label="Decorative vertical rules beside the arch"
          d="M 34 922 L 172 892 L 172 1048 L 34 1050 Z" fill="url(#rule-tone-left)"/>
    <path class="rule-ornament rule-ornament-right" role="img" aria-label="Decorative vertical rules beside the arch"
          d="M 968 892 L 1106 922 L 1106 1050 L 968 1048 Z" fill="url(#rule-tone-right)"/>

    <text class="brand-name" font-size="150">
      <textPath href="#brand-arc" startOffset="50%" text-anchor="middle" textLength="1880" lengthAdjust="spacing">DUNMORE VALE</textPath>
    </text>

    <path class="info-panel" d="M 4 1052 Q 570 1015 1136 1052 C 1120 1300 870 1466 570 1466 C 270 1466 20 1300 4 1052 Z"
          fill="var(--ink)"/>

    <text class="varietal-line" x="570" y="1130" font-size="62" text-anchor="middle">NEW ZEALAND</text>
    <text class="varietal-line" x="570" y="1200" font-size="62" text-anchor="middle">MARLBOROUGH</text>
    <text class="varietal-line" x="570" y="1270" font-size="62" text-anchor="middle">SAUVIGNON BLANC</text>
    <text class="vintage" x="570" y="1342" font-size="56" text-anchor="middle">•2023•</text>
    <text class="cuvee-note" x="570" y="1400" font-size="34" text-anchor="middle">LOREM IPSUM</text>
  </svg>
</main>
</body>
</html>
```